High-end Oceanfront Real Estate Group Needs Clean, Modern Web Design

I’m looking for a clean, professional, modern and beautiful homepage web design for a Real Estate group in Southern California, USA.

The group/company is “Marwick on the Shore,” and they specialize in high end (i.e. expensive), oceanfront real estate in the Orange County area.

The look and feel of the page should accentuate the brand qualities: luxurious/expensive, professional, and beautiful (Orange County is one of the most beautiful areas in all the US and we would love the site to emphasize the beautiful beaches and scenery it has to offer).

Looks we like:
• www.brantleyhomesrealty.example
• www.closedbyvane.example -- I think the design is pretty out-dated in this site, but I like the organization/layout of the site

Header Tags (I don’t know if we can fit all of these, may need a side-menu, but I’d prefer header title only if possible):
• Welcome
• Featured Listings
• Previously Sold
• Sell
• Property Search
• Team
• Videos
• Blog
• Explore O.C.
• Contact

I have attached the beach and logo pics that we would like to use as the header, a few pictures of the team, and one sample home/view pic which can be used in any of the other sections (for pictures of the homes, just find expensive oceanfront houses and that will be fine).

I promise to provide feedback to each and every design submission. I appreciate the hard work that all of you are putting into your designs. There can be only one contest winner, but I hope to give all of you helpful feedback to submit the best designs possible!

Target Market(s)

Very wealthy home owners of oceanfront properties. These properties are worth several millions of dollars, and thus the site and brand needs to be targeted to very wealthy, successful individuals and families (both US and international buyers).

Industry/Entity Type

Real Estate

Number of Pages Required

2 page

Requirements
Must have
• I don’t want to give too many requirements, because I want to let you all be creative. However, here are the few Must Haves:
• Must submit 2 page designs (a home page and a sub page)
• Must use logo provided
• Focus is mostly on homes, but I would like to include some beach/ocean imagery as well
• The first “item” on the home page should be an accordion/slider which shows pictures of homes and with 1 line of text: “List with the Leader” and two link buttons: “Sell Your Home” and “Buy Your Home”
• Color palette needs to be mainly blues--to match ocean and sky blue
• Exported in all major formats (psd,ai,eps,png,jpeg,etc)
Nice to have
• We don’t necessarily need all of these, but would like to feature most:
• List of videos
• “Meet the Team”—brief team bios and pics
• Link(s) to Blog
• “List with the Leader” – section on why they should choose this firm
• Featured Listings
• Previously Sold

```html
<!DOCTYPE html>
<html lang="en">
<head>
<meta charset="utf-8">
<title>Marwick on the Shore — Home</title>
<link rel="stylesheet" href="https://fonts.googleapis.com/css2?family=Raleway:wght@400;500;600;700&family=Open+Sans:wght@400;600;700&family=Oswald:wght@500&display=swap">
<style>
:root{
  --blue:#1a68ad;
  --blue-dark:#155a97;
  --ink:#333333;
  --muted:#666666;
  --band:#f4f4f4;
  --band-grey:#e4e3e3;
  --orange:#e8921e;
  --footer:#2e2e2e;
  --footer-bottom:#1e1e1e;
  --footer-text:#9a9a9a;
  --white:#ffffff;
}
*{box-sizing:border-box;margin:0;padding:0}
html,body{width:1200px;height:2628px;overflow:hidden}
body{position:relative;background:var(--white);font-family:"Open Sans",Arial,sans-serif;color:var(--ink)}
.abs{position:absolute}
.center{left:0;width:1200px;text-align:center}

/* hero */
.hero{position:absolute;left:0;top:0;width:1200px;height:601px;
  background:linear-gradient(180deg,#1c3f9e 0%,#3a6fc2 28%,#7fb2da 40%,#2f86a8 52%,#1d6f86 70%,#c8b99a 92%,#d9cdb3 100%)}
.brand{position:absolute;left:110px;top:0;width:230px;height:156px;background:var(--blue);border:2px solid rgba(255,255,255,.85);border-top:0;display:flex;align-items:center;justify-content:center}
.brand-name{font-family:"Raleway",sans-serif;font-weight:500;color:var(--white);font-size:26px;line-height:1.15;text-align:center;letter-spacing:1px}
.nav{position:absolute;left:396px;top:64px;display:flex;gap:4px}
.nav a{font-family:"Open Sans",sans-serif;font-size:13px;color:var(--white);text-decoration:none;padding:9px 12px;border-radius:3px;text-transform:uppercase}
.nav a.active{background:rgba(40,40,40,.85)}
.hero-title{top:270px;font-family:"Raleway",sans-serif;font-weight:700;font-size:35px;color:var(--white);letter-spacing:.5px}
.hero-sub{top:322px;font-family:"Raleway",sans-serif;font-size:18px;line-height:32px;color:var(--white)}
.hero-arrow{position:absolute;top:287px;width:32px;height:32px}
.thumbs{position:absolute;left:110px;top:527px;width:980px;height:74px;background:var(--white);padding:5px 5px 0;display:flex;gap:6px}
.thumb{flex:1;height:69px}

/* section headings */
.sec-title{font-family:"Raleway",sans-serif;font-weight:400;font-size:31px;color:var(--ink);letter-spacing:.5px}
.sec-title b{color:var(--blue);font-weight:600}
.lede{font-size:13px;line-height:24px;color:var(--muted)}

.btn{position:absolute;font-family:"Open Sans",sans-serif;font-weight:600;font-size:16px;text-align:center}
.btn-solid{background:var(--blue);color:var(--white);line-height:51px}
.btn-ghost{background:var(--white);color:#555;border:3px solid #ddd;line-height:45px}

/* featured */
.featured{position:absolute;left:0;top:900px;width:1200px;height:584px;background:var(--band)}
.card{position:absolute;top:193px;width:204px}
.card-photo{width:204px;height:137px}
.card-title{margin-top:15px;font-size:14px;font-weight:600;color:var(--blue)}
.card-text{margin-top:4px;font-size:12.5px;line-height:23px;color:var(--muted)}
.card-text a{color:var(--blue);font-weight:600;text-decoration:none}
.card-btn{margin-top:18px;display:inline-block;background:var(--blue);color:var(--white);font-size:12.5px;font-weight:600;padding:6px 8px;border-radius:2px}
.slide-arrow{position:absolute;top:241px;width:24px;height:30px;background:#e2e2e2;border:1px solid #d4d4d4}
.pager{position:absolute;top:525px;display:flex;gap:12px;left:553px}
.pager span{width:26px;height:26px;line-height:26px;text-align:center;font-size:14px;font-weight:600;background:#ddd;color:#444}
.pager span.on{background:var(--blue);color:var(--white)}

/* why */
.col-title{font-family:"Raleway",sans-serif;font-size:28px;color:#222}
.col-title b{color:var(--blue);font-weight:600}
.col-sub{font-family:"Raleway",sans-serif;font-weight:700;font-size:17px;color:#222;text-transform:uppercase}
.col-text{font-size:12.5px;line-height:26px;color:#555}
.checks{list-style:none}
.checks li{display:flex;align-items:center;gap:16px;height:28px;font-size:15px;color:var(--blue)}
.divider{position:absolute;left:590px;top:1673px;width:1px;height:403px;background:linear-gradient(180deg,transparent,#ddd 15%,#ddd 85%,transparent)}
.video{position:absolute;left:649px;top:1789px;width:442px;height:250px;background:linear-gradient(180deg,#2f6fb0 0%,#4f8dc4 40%,#2a8c9a 70%,#b9ab8f 100%)}
.video-bar{position:absolute;left:0;bottom:0;width:100%;height:18px;background:#1b1b1b}
.video-top{position:absolute;left:0;top:0;width:100%;height:22px;background:rgba(0,0,0,.55)}

/* start band */
.start{position:absolute;left:0;top:2130px;width:1200px;height:228px;background:var(--band-grey)}
.start-form{position:absolute;left:110px;top:106px;width:980px;height:87px;background:#d2d1d1;border-radius:4px}
.field{position:absolute;top:21px;height:47px;background:var(--white);border:1px solid #ccc;font-size:13px;color:#777;padding:0 14px;line-height:45px}
.cta{position:absolute;left:762px;top:21px;width:197px;height:47px;background:var(--orange);color:var(--white);font-family:"Oswald",sans-serif;font-size:21px;text-align:center;line-height:47px;border-radius:2px}

/* footer */
.footer{position:absolute;left:0;top:2358px;width:1200px;height:217px;background:var(--footer)}
.skyline{position:absolute;left:0;bottom:0;width:1200px;height:70px}
.f-col{position:absolute;top:40px}
.f-col h4{font-family:"Raleway",sans-serif;font-weight:500;font-size:15px;color:#e6e6e6;text-transform:uppercase;border-bottom:1px solid #555;padding-bottom:6px;margin-bottom:8px;width:122px}
.f-col p{font-size:12px;line-height:26px;color:var(--footer-text)}
.f-contact p{font-size:12px;line-height:26px;color:var(--footer-text)}
.social{display:flex;gap:14px;margin-top:14px}
.social span{width:24px;height:24px;border-radius:50%;background:#6f6f6f}
.bottom{position:absolute;left:0;top:2575px;width:1200px;height:53px;background:var(--footer-bottom);font-size:12px;color:var(--footer-text);line-height:53px}
</style>
</head>
<body>

<header class="hero" role="img" aria-label="Tropical beach with palm trees, turquoise sea and rocks under a blue sky">
  <div class="brand"><div class="brand-name">MARWICK<br>ON THE SHORE</div></div>
  <nav class="nav">
    <a class="active">Home</a><a>Featured Listings</a><a>Sold</a><a>Sell</a><a>Team</a><a>Videos</a><a>Blog</a><a>Contact</a>
  </nav>
  <h1 class="abs center hero-title">WE ARE OFFERING THE BEST REAL ESTATE DEALS</h1>
  <p class="abs center hero-sub">WE AT MARWICKONTHESHORE ARE PRIVILEGED TO HELP PEOPLE FROM ALL OVER THE WORLD<br>FIND THEIR DREAM HOMES</p>
  <svg class="hero-arrow" style="left:47px" viewBox="0 0 32 32"><circle cx="16" cy="16" r="14" fill="none" stroke="#fff" stroke-width="2"/><path d="M18 10l-6 6 6 6" fill="none" stroke="#fff" stroke-width="2.4"/></svg>
  <svg class="hero-arrow" style="left:1119px" viewBox="0 0 32 32"><circle cx="16" cy="16" r="14" fill="none" stroke="#fff" stroke-width="2"/><path d="M14 10l6 6-6 6" fill="none" stroke="#fff" stroke-width="2.4"/></svg>
  <div class="thumbs">
    <div class="thumb" role="img" aria-label="Palm trees over the sea" style="background:linear-gradient(180deg,#4a74a8,#2d5e86)"></div>
    <div class="thumb" role="img" aria-label="Turquoise lagoon" style="background:linear-gradient(180deg,#3a8fa0,#2fb5b0)"></div>
    <div class="thumb" role="img" aria-label="Overwater villas" style="background:linear-gradient(180deg,#5aa6d8,#3cc2c8)"></div>
    <div class="thumb" role="img" aria-label="Beach shoreline" style="background:linear-gradient(180deg,#50719a,#7f8d92)"></div>
    <div class="thumb" role="img" aria-label="Coastal bay" style="background:linear-gradient(180deg,#2c6ea6,#1f8fa6)"></div>
    <div class="thumb" role="img" aria-label="Beach house terrace" style="background:linear-gradient(180deg,#6f9cc8,#a9b4b5)"></div>
  </div>
</header>

<section>
  <h2 class="abs center sec-title" style="top:652px">WELCOME TO <b>MARWICK ON THE SHORE</b></h2>
  <p class="abs center lede" style="top:710px">Lorem ipsum dolor sit amet, consectetur adipiscing elit, sed do eiusmod tempor incididunt ut labore et dolore magna aliqua. Ut enim<br>ad minim veniam, quis nostrud exercitation ullamco laboris nisi ut aliquip ex ea commodo consequat.</p>
  <div class="btn btn-solid" style="left:408px;top:783px;width:183px;height:51px">Sell Your Home</div>
  <div class="btn btn-ghost" style="left:608px;top:783px;width:175px;height:51px">Buy Your Home</div>
</section>

<section class="featured">
  <h2 class="abs center sec-title" style="top:36px">FEATURED <b>LISTING</b></h2>
  <p class="abs center lede" style="top:86px">Lorem ipsum dolor sit amet, consectetur adipiscing elit, sed do eiusmod tempor incididunt ut labore et dolore magna aliqua. Ut enim<br>ad minim veniam, quis nostrud exercitation ullamco laboris nisi ut aliquip ex ea commodo consequat.</p>
  <div class="slide-arrow" style="left:111px"></div>
  <div class="slide-arrow" style="left:1066px"></div>
  <div class="card" style="left:152px">
    <div class="card-photo" role="img" aria-label="Lit hillside villa at dusk above a bay" style="background:linear-gradient(180deg,#3f6ea6,#6a6a7c 60%,#5a5040)"></div>
    <div class="card-title">Lorem ipsum</div>
    <div class="card-text">Lorem ipsum dolor sit amet,<br>consectetur...<a>Know More</a></div>
    <div class="card-btn">View the listing</div>
  </div>
  <div class="card" style="left:382px">
    <div class="card-photo" role="img" aria-label="Beach house with deck by the sea" style="background:linear-gradient(180deg,#8cc1ea,#d4d8d6 60%,#7a9aa8)"></div>
    <div class="card-title">Lorem ipsum</div>
    <div class="card-text">Lorem ipsum dolor sit amet,<br>consectetur...<a>Know More</a></div>
    <div class="card-btn">View the listing</div>
  </div>
  <div class="card" style="left:612px">
    <div class="card-photo" role="img" aria-label="Overwater pavilion at sunset" style="background:linear-gradient(180deg,#2f4f7f,#e9a24a 45%,#1f5f9a)"></div>
    <div class="card-title">Lorem ipsum</div>
    <div class="card-text">Lorem ipsum dolor sit amet,<br>consectetur...<a>Know More</a></div>
    <div class="card-btn">View the listing</div>
  </div>
  <div class="card" style="left:844px">
    <div class="card-photo" role="img" aria-label="Thatched deck over the water at sunrise" style="background:linear-gradient(180deg,#f0a030,#c27028 45%,#1e6fb5)"></div>
    <div class="card-title">Lorem ipsum</div>
    <div class="card-text">Lorem ipsum dolor sit amet,<br>consectetur...<a>Know More</a></div>
    <div class="card-btn">View the listing</div>
  </div>
  <div class="pager"><span class="on">1</span><span>2</span><span>3</span></div>
</section>

<section>
  <h2 class="abs center sec-title" style="top:1529px">WHY MARWICK ON THE SHORE</h2>
  <p class="abs center lede" style="top:1586px">Lorem ipsum dolor sit amet, consectetur adipiscing elit, sed do eiusmod tempor incididunt ut labore et dolore magna aliqua. Ut enim<br>ad minim veniam, quis nostrud exercitation ullamco laboris nisi ut aliquip ex ea commodo consequat.</p>

  <div class="abs" style="left:110px;top:1700px;width:460px">
    <h3 class="col-title">About <b>MARWICK ON THE SHORE</b></h3>
    <h4 class="col-sub" style="margin-top:22px">Lorem ipsum dolor sit amet, consectetur</h4>
    <p class="col-text" style="margin-top:6px">adipiscing elit, sed do eiusmod tempor incididunt ut labore et dolore magna aliqua ut enim ad minim veniam, quis nostrud exercitation ullamco laboris nisi ut aliquip.</p>
    <h4 class="col-sub" style="margin-top:18px">Lorem ipsum dolor sit amet, consectetur</h4>
    <ul class="checks" style="margin-top:10px">
      <li><svg width="18" height="16" viewBox="0 0 18 16"><path d="M1 8l5 6L17 1" fill="none" stroke="#222" stroke-width="2.6"/></svg>Lorem ipsum sit amet</li>
      <li><svg width="18" height="16" viewBox="0 0 18 16"><path d="M1 8l5 6L17 1" fill="none" stroke="#222" stroke-width="2.6"/></svg>Consectetur amet</li>
      <li><svg width="18" height="16" viewBox="0 0 18 16"><path d="M1 8l5 6L17 1" fill="none" stroke="#222" stroke-width="2.6"/></svg>Dolor sit amet consectetur</li>
      <li><svg width="18" height="16" viewBox="0 0 18 16"><path d="M1 8l5 6L17 1" fill="none" stroke="#222" stroke-width="2.6"/></svg>Lorem Ipsum sit amet</li>
    </ul>
  </div>
  <div class="divider"></div>

  <div class="abs" style="left:650px;top:1700px;width:460px">
    <h3 class="col-title">Our <b>VIDEOS</b> <span style="font-size:15px;font-weight:700">LOREM IPSUM DOLOR SIT AMET.</span></h3>
    <p class="col-text" style="margin-top:4px">adipiscing elit, sed do eiusmod tempor incididunt ut labore et dolore</p>
  </div>
  <div class="video" role="img" aria-label="Video still of a palm-lined tropical beach">
    <div class="video-top"></div>
    <svg class="abs" style="left:193px;top:98px" width="56" height="56" viewBox="0 0 56 56"><circle cx="28" cy="28" r="27" fill="rgba(20,20,20,.75)"/><path d="M22 17l17 11-17 11z" fill="#fff"/></svg>
    <div class="video-bar"></div>
  </div>
</section>

<section class="start">
  <h2 class="abs center" style="top:22px;font-family:'Raleway',sans-serif;font-size:30px;color:#444">Ok Let’s Get Started Now. Its Free</h2>
  <p class="abs center" style="top:68px;font-size:14px;color:#666">Post your Retail Space requirement with us and our experts shall get back with suitable options and even help you</p>
  <div class="start-form">
    <div class="field" style="left:27px;width:228px">Enter Email</div>
    <div class="field" style="left:272px;width:228px">Mobile</div>
    <div class="field" style="left:517px;width:228px">Add Description of Requirment</div>
    <div class="cta">VIEW MORE</div>
  </div>
</section>

<footer class="footer">
  <svg class="skyline" viewBox="0 0 1200 70" preserveAspectRatio="none" aria-hidden="true"><path d="M0 70V40h30V22h24v18h20V30h26v40h10V10h30v60h20V35h40v35h30V25h22v45h40V44h30v26h40V18h26v52h30V36h50v34h40V28h20v42h50V40h30v30h40V20h30v50h30V34h50v36h40V26h30v44h40V42h30v28h40V16h26v54h40V38h60v32h40V30h40v40z" fill="#383838"/></svg>
  <div class="f-col" style="left:135px"><h4>About Us</h4><p>About Us<br>Privacy Policy<br>Terms of Use<br>Contact Us<br>Site Map</p></div>
  <div class="f-col" style="left:298px"><h4>About Us</h4><p>Retail Malls<br>Shopping Complex<br>High Street Shops<br>Retail Warehouses</p></div>
  <div class="f-col" style="left:466px"><h4>Community</h4><p>Blog<br>Support<br>Translation Tool<br>Developer</p></div>
  <div class="f-col" style="left:641px"><h4>Support Us</h4><p>Knowledgebase<br>Download &amp; Update<br>Information<br>Documentation</p></div>
  <div class="f-contact abs" style="left:841px;top:36px">
    <p>Harborview Lane 1200<br>LAGUNA POINT, CA 92651<br>Phone: +1 (949) 555 0142<br>Email: info@marwickshore.example</p>
    <div class="social"><span></span><span></span><span></span></div>
  </div>
</footer>
<div class="bottom">
  <span class="abs" style="left:110px">Copyrights © 2014 Marwick on the Shore - All Rights Reserved</span>
  <span class="abs" style="left:885px">Privacy Policy &nbsp;&nbsp;|&nbsp;&nbsp; Terms &amp; Condition</span>
</div>

</body>
</html>
```